Lime Wash Direct Mail Postcard Design

I need a postcard that is going to be mailed.
We are a residential and commerical painting company. We are going to start marking our Ventian Plaster, Lime Wash, Roman Clay, Mineral Wash.
I've attached the layout to use that shows bleed and such. I've included a mock up I've done to get an idea of what I want.
- I want it to look sophicated
- Speciality
- Art
I've included logos of 2 companies - Velunta and Fendrix to show.
I want to show mostly interior work but one or 2 lime wash houses that's lighter, shows the bricks in area would be good.
I love the saying "You're unique - Your Home Should Be Too" or if you have a better variation of that, I'd be open to it.

```html
<!DOCTYPE html>
<html lang="en">
<head>
<meta charset="utf-8">
<title>Brightwall Painting – Postcard Front</title>
<link href="https://fonts.googleapis.com/css2?family=Days+One&display=swap" rel="stylesheet">
<style>
  :root {
    --stage: #a8a8a8;
    --paper: #ececec;
    --brand-blue: #5795d0;
    --brand-red: #c8373b;
    --overlap: #5c3645;
    --ink: #151515;
    --gold: #c9ad78;
    --white: #ffffff;
  }
  * { margin: 0; padding: 0; box-sizing: border-box; }
  html, body {
    width: 1200px; height: 1200px; overflow: hidden;
    background: var(--stage);
  }
  .postcard {
    position: absolute; left: 50px; top: 216px;
    width: 1100px; height: 768px;
    background: var(--paper);
    overflow: hidden;
    box-shadow: 0 3px 8px rgba(0,0,0,.25);
    font-family: "Days One", sans-serif;
  }
  .postcard__art { position: absolute; inset: 0; width: 100%; height: 100%; }
  .offer { position: absolute; left: 674px; top: 0; width: 400px; height: 100%; }
  .brand {
    position: absolute; left: 20px; top: 118px;
    display: flex; align-items: center; gap: 10px;
    color: var(--brand-blue); font-size: 24px; letter-spacing: .5px;
  }
  .brand__mark { width: 22px; height: 22px; background: var(--brand-red); }
  .headline {
    position: absolute; left: 20px; top: 222px;
    color: var(--brand-blue); font-size: 46px; line-height: 54px;
  }
  .tag {
    position: absolute; left: 0; width: 388px;
    background: var(--brand-red); color: var(--white);
    text-align: center;
  }
  .tag--tagline { top: 343px; height: 58px; font-size: 25px; line-height: 58px; }
  .consult {
    position: absolute; left: 2px; top: 412px;
    color: var(--brand-blue); font-size: 36px; white-space: nowrap;
  }
  .discount {
    position: absolute; left: -22px; top: 452px;
    color: var(--brand-blue); font-size: 162px; line-height: 160px; letter-spacing: -3px;
    white-space: nowrap;
  }
  .discount__off {
    position: absolute; left: 318px; top: 458px;
    color: var(--brand-red); font-size: 26px; line-height: 28px;
  }
  .tag--deadline { top: 614px; height: 60px; font-size: 44px; line-height: 60px; }
  .partners {
    position: absolute; left: 12px; top: 698px; width: 376px;
    display: flex; align-items: center; justify-content: space-between;
    font-size: 25px; letter-spacing: .5px;
  }
  .partner--velunta { color: var(--ink); }
  .partner--fendrix { color: var(--gold); }
</style>
</head>
<body>
  <section class="postcard">
    <svg class="postcard__art" viewBox="0 0 1020 712" preserveAspectRatio="none">
      <defs>
        <clipPath id="blue-arc-clip">
          <ellipse cx="250" cy="350" rx="345" ry="400"/>
        </clipPath>
        <linearGradient id="kitchen-tones" x1="0" y1="0" x2="0" y2="1">
          <stop offset="0" stop-color="#e4e4e2"/>
          <stop offset=".45" stop-color="#c9ad88"/>
          <stop offset=".7" stop-color="#a8a29a"/>
          <stop offset="1" stop-color="#d9c2a0"/>
        </linearGradient>
      </defs>
      <ellipse class="arc-blue" cx="250" cy="350" rx="345" ry="400" fill="var(--brand-blue)"/>
      <path class="wedge-red" d="M548 400 C585 500 610 620 620 712 L190 712 C330 640 470 540 548 400 Z" fill="var(--brand-red)"/>
      <path class="wedge-overlap" clip-path="url(#blue-arc-clip)" d="M548 400 C585 500 610 620 620 712 L190 712 C330 640 470 540 548 400 Z" fill="var(--overlap)"/>
      <circle class="photo" role="img" aria-label="Photo of a bright modern kitchen with wood cabinets, white brick tiles, washing machine, oven and a green armchair" cx="240" cy="345" r="310" fill="url(#kitchen-tones)" stroke="var(--white)" stroke-width="4"/>
    </svg>

    <div class="offer">
      <div class="brand"><span class="brand__mark"></span><span>BRIGHTWALL PAINTING</span></div>
      <h1 class="headline">YOU’RE<br>UNIQUE</h1>
      <p class="tag tag--tagline">Your home should be too</p>
      <p class="consult">Free consultation</p>
      <p class="discount">10%</p>
      <span class="discount__off">OFF</span>
      <p class="tag tag--deadline">thru Jan 31st</p>
      <div class="partners">
        <span class="partner--velunta">VELUNTA</span>
        <span class="partner--fendrix">FENDRIX</span>
      </div>
    </div>
  </section>
</body>
</html>
```